Yacht, Boats, Watersports company needs a redesign of business card

Hello Designers!
We are a Boat dealership company that sells fun in the water, we sell boats, Yachts, Kayaks and also yacht WaterSport toys. We are looking to redesign our business cards in to something a little bit more sophisticated. in a way that we can make better use of our company colors. I'm attaching a zipped file containing the company 3 sets of company logo which one is an horizontal another one is a vertical and also a chromed 3d logo. Also is included two set of business cards that we use and also some designs that i think it's interesting. We use PMS 2026c Orange and PMS 7687C Blue. I would like to see at least two different options with the orange as accent and also using blue as an accent color. It's really important for the business cards to have a font option and size that is legible to most people. Our current website is wwww.coralpennant.com. Please visit if you want to have a better feeling of the Boat dealership
You can send Single sided or double side options. We are now using single sided but we may be open for a double side option if we really like the design.
Target Market(s)
Marine, boat sales, yacht sales, water toys sales/
Contact Information for Business Card
Name: Dale Whitcombe
Address: 212 North Fenwick Lane,
Seabright Key, FL 33912
Phone: 954-731-8842
Fax: 954:731-8843
Cell: 954-382-1490
Email: dw@coralpennant.com
Website: coralpennant.com
Requirements
Must have
- the current information of the business card provided.
logo
use the PMS Colors
Nice to have
- a touch of elegance and sophistication but simple
Should not have
- should not have any typography that is hard to read, the card should be simple but yet sophisticated.

```html
<!DOCTYPE html>
<html lang="en">
<head>
<meta charset="utf-8">
<title>Coral Pennant – Business Card</title>
<link rel="stylesheet" href="https://fonts.googleapis.com/css2?family=Lato:wght@400;700;900&display=swap">
<style>
  :root {
    --brand-blue: #134a86;
    --brand-orange: #f26a2e;
    --card-white: #ffffff;
    --text-grey: #7a7a7a;
    --backdrop: #e9ebee;
    --card-radius: 28px;
  }
  * { box-sizing: border-box; margin: 0; padding: 0; }
  html, body {
    width: 1200px; height: 900px; overflow: hidden;
    background: var(--backdrop);
    font-family: "Lato", Arial, sans-serif;
  }
  .sheet { position: relative; width: 1200px; height: 900px; }
  .card {
    position: absolute; left: 250px; width: 700px; height: 400px;
    border-radius: var(--card-radius); overflow: hidden;
    box-shadow: 0 10px 30px rgba(0,0,0,.15);
  }

  /* Back side */
  .card-back { top: 40px; background: var(--brand-blue); }
  .card-back .pattern-field {
    position: absolute; inset: 0;
    background: linear-gradient(135deg, #1a5596 0%, var(--brand-blue) 60%, #104078 100%);
  }
  .card-back .brand {
    position: absolute; left: 50%; top: 50%; transform: translate(-50%, -50%);
    display: flex; align-items: center; gap: 14px; white-space: nowrap;
  }
  .card-back .brand-dot {
    width: 24px; height: 24px; border-radius: 50%; background: var(--brand-orange); flex: none;
  }
  .card-back .brand-name {
    font-weight: 900; font-size: 32px; letter-spacing: 3px;
    color: var(--card-white); text-transform: uppercase;
  }

  /* Front side */
  .card-front { top: 460px; background: var(--card-white); }
  .card-front .emblem-field {
    position: absolute; right: 0; top: 0; width: 280px; height: 400px;
    background: linear-gradient(160deg, rgba(242,106,46,.22) 0%, rgba(242,106,46,.08) 45%, rgba(19,74,134,.18) 100%);
  }
  .card-front .brand-name {
    position: absolute; left: 48px; top: 96px; white-space: nowrap;
    font-weight: 900; font-size: 24px; letter-spacing: 2.5px;
    color: var(--brand-blue); text-transform: uppercase;
  }
  .card-front .details { position: absolute; left: 70px; top: 150px; }
  .person-name {
    font-weight: 700; font-size: 34px; line-height: 1; text-transform: uppercase;
    color: var(--brand-blue); white-space: nowrap;
  }
  .person-name .surname { color: var(--brand-orange); }
  .person-title { color: var(--text-grey); font-size: 17px; margin-top: 6px; }
  .address { color: var(--text-grey); font-size: 16px; line-height: 1.25; margin: 12px 0 0 14px; }
  .contacts { list-style: none; margin: 10px 0 0 14px; }
  .contacts li {
    display: flex; align-items: center; gap: 10px;
    color: var(--text-grey); font-size: 15.5px; line-height: 21px;
  }
  .contacts svg { width: 15px; height: 15px; fill: var(--brand-blue); flex: none; }
</style>
</head>
<body>
<main class="sheet">

  <section class="card card-back" aria-label="Business card back">
    <div class="pattern-field" role="img" aria-label="Faint repeating brand pattern on blue"></div>
    <div class="brand">
      <span class="brand-dot"></span>
      <span class="brand-name">Coral Pennant</span>
    </div>
  </section>

  <section class="card card-front" aria-label="Business card front">
    <div class="emblem-field" role="img" aria-label="Large brand decoration in orange and blue"></div>
    <div class="brand-name">Coral Pennant</div>

    <div class="details">
      <h1 class="person-name">Dale <span class="surname">Whitcombe</span></h1>
      <p class="person-title">Founder &amp; CEO</p>
      <p class="address">212 North Fenwick Lane,<br>Seabright Key, FL 33912</p>
      <ul class="contacts">
        <li>
          <svg viewBox="0 0 16 16" aria-hidden="true"><path d="M1 5c0-2 3-3 7-3s7 1 7 3v1h-3V5H4v1H1z"/><rect x="3" y="7" width="10" height="7" rx="1"/></svg>
          954-731-8842
        </li>
        <li>
          <svg viewBox="0 0 16 16" aria-hidden="true"><path d="M4 0h8a1 1 0 0 1 1 1v14a1 1 0 0 1-1 1H4a1 1 0 0 1-1-1V1a1 1 0 0 1 1-1zm1 2v10h6V2z"/></svg>
          954-382-1490
        </li>
        <li>
          <svg viewBox="0 0 16 16" aria-hidden="true"><rect x="4" y="1" width="8" height="4"/><rect x="1" y="6" width="14" height="6" rx="1"/><rect x="4" y="10" width="8" height="5"/></svg>
          954:731-8843
        </li>
        <li>
          <svg viewBox="0 0 16 16" aria-hidden="true"><path d="M1 3h14v10H1zm1.5 1.2L8 8.5l5.5-4.3z"/></svg>
          dw@coralpennant.com
        </li>
        <li>
          <svg viewBox="0 0 16 16" aria-hidden="true"><path d="M8 1a7 7 0 1 0 0 14A7 7 0 0 0 8 1zm0 1.5c.8 0 1.7 1.9 1.9 4.7H6.1C6.3 4.4 7.2 2.5 8 2.5zm-3.4 4.7H2.6a5.5 5.5 0 0 1 3.3-4.3c-.7 1.1-1.2 2.6-1.3 4.3zm0 1.6c.1 1.7.6 3.2 1.3 4.3a5.5 5.5 0 0 1-3.3-4.3zm1.5 0h3.8c-.2 2.8-1.1 4.7-1.9 4.7s-1.7-1.9-1.9-4.7zm5.3 0h2a5.5 5.5 0 0 1-3.3 4.3c.7-1.1 1.2-2.6 1.3-4.3zm0-1.6c-.1-1.7-.6-3.2-1.3-4.3a5.5 5.5 0 0 1 3.3 4.3z"/></svg>
          www.coralpennant.com
        </li>
      </ul>
    </div>
  </section>

</main>
</body>
</html>
```